New Business Card Design

We would like to refresh our business cards and make them look better. We are an IT company specialising in Cloud Services, IT Managed Services, software and hardware. I have attached a PSD of our current design. Also attached our logo.
Updates

I have uploaded all new logos in EPS format.

Can you please edit all designs to include a job title for Marcus Hollis, eg. General Manager

Industry/Entity Type

Software

Colors
ffffff

Requirements
Must have
• Please use white background.
Should not have
• Black background

```html
<!DOCTYPE html>
<html lang="en">
<head>
<meta charset="utf-8">
<title>Calverwick Tech – Business Card</title>
<link rel="stylesheet" href="https://fonts.googleapis.com/css2?family=Open+Sans:wght@300;400;600&display=swap">
<style>
  :root {
    --page: #ecebe8;
    --card-white: #ffffff;
    --card-grey-top: #f7f7f7;
    --card-grey-bottom: #dedfe0;
    --brand-red: #c4302b;
    --brand-grey: #8a939c;
    --ink: #3a3a3a;
    --ink-soft: #555a5f;
    --faint: #efefef;
  }
  * { box-sizing: border-box; margin: 0; padding: 0; }
  html, body {
    width: 1200px; height: 720px; overflow: hidden;
    background: var(--page);
    font-family: "Open Sans", Arial, sans-serif;
    color: var(--ink);
  }
  .canvas {
    position: relative; width: 1200px; height: 720px;
    display: flex; align-items: center; justify-content: center; gap: 40px;
  }
  .card {
    position: relative; width: 540px; height: 309px; overflow: hidden;
    box-shadow: 0 6px 18px rgba(0,0,0,0.18);
  }

  .brand { display: flex; align-items: center; gap: 14px; }
  .brand-dot {
    width: 44px; height: 44px; border-radius: 50%; background: var(--brand-red); flex: none;
  }
  .brand-name {
    font-weight: 300; font-size: 28px; letter-spacing: 3px; color: var(--ink);
    line-height: 1; white-space: nowrap;
  }

  /* Front: contact side */
  .card-front { background: var(--card-white); }
  .edge-band {
    position: absolute; left: 0; top: 0; width: 14px; height: 100%;
    background: linear-gradient(to bottom, var(--brand-red) 0 48%, var(--brand-grey) 48% 100%);
  }
  .card-front .brand { position: absolute; left: 48px; top: 38px; }
  .faint-mark {
    position: absolute; right: 24px; top: 100px; width: 128px; height: 128px;
    border-radius: 50%; background: var(--faint);
  }
  .holder { position: absolute; left: 48px; top: 150px; white-space: nowrap; }
  .holder-name { font-weight: 600; font-size: 17px; color: var(--brand-red); }
  .holder-title { font-weight: 400; font-size: 14px; color: var(--ink); }
  .contacts { position: absolute; left: 48px; top: 192px; list-style: none; }
  .contacts li {
    display: flex; align-items: center; gap: 10px;
    font-size: 13.5px; color: var(--ink-soft); line-height: 23px; white-space: nowrap;
  }
  .contacts svg { width: 15px; height: 15px; flex: none; }

  /* Back: tagline side */
  .card-back {
    background: linear-gradient(160deg, var(--card-grey-top) 0%, var(--card-white) 40%, var(--card-grey-bottom) 100%);
  }
  .card-back .brand {
    position: absolute; left: 0; right: 0; top: 60px; justify-content: center;
  }
  .tagline {
    position: absolute; left: 0; right: 0; top: 156px; text-align: center;
    font-size: 17px; line-height: 27px; color: var(--ink);
  }
  .web {
    position: absolute; left: 0; right: 0; top: 236px; text-align: center;
    font-size: 14px; letter-spacing: 2.5px; color: var(--ink-soft);
  }
  .web-domain { color: var(--brand-red); font-weight: 600; }
</style>
</head>
<body>
<main class="canvas">
  <section class="card card-front" aria-label="Business card front">
    <div class="edge-band"></div>
    <div class="faint-mark"></div>
    <div class="brand">
      <span class="brand-dot"></span>
      <span class="brand-name">calverwick tech</span>
    </div>
    <div class="holder">
      <span class="holder-name">Marcus Hollis,</span>
      <span class="holder-title">General Manager</span>
    </div>
    <ul class="contacts">
      <li>
        <svg viewBox="0 0 16 16" aria-hidden="true"><circle cx="8" cy="8" r="8" fill="#c4302b"/><path d="M5 4.5c.5-.5 1.2-.5 1.5 0l.7 1.3c.2.4 0 .8-.3 1l-.5.4c.5 1 1.2 1.7 2.2 2.2l.4-.5c.3-.3.7-.5 1-.3l1.3.7c.5.3.5 1 0 1.5-.8.8-2 .9-3.3 0-1.4-.9-2.4-2-3.2-3.3-.7-1.3-.6-2.3.2-3z" fill="#fff"/></svg>
        07 5550 3182
      </li>
      <li>
        <svg viewBox="0 0 16 16" aria-hidden="true"><circle cx="8" cy="8" r="8" fill="#c4302b"/><rect x="5.5" y="3.5" width="5" height="9" rx="1" fill="#fff"/><rect x="6.3" y="4.6" width="3.4" height="5.6" fill="#c4302b"/></svg>
        0491 570 156
      </li>
      <li>
        <svg viewBox="0 0 16 16" aria-hidden="true"><circle cx="8" cy="8" r="8" fill="#c4302b"/><rect x="4" y="5" width="8" height="6" fill="#fff"/><path d="M4 5l4 3.2L12 5" stroke="#c4302b" stroke-width="1" fill="none"/></svg>
        marcush@calverwickit.com.au
      </li>
      <li>
        <svg viewBox="0 0 16 16" aria-hidden="true"><circle cx="8" cy="8" r="8" fill="#c4302b"/><circle cx="8" cy="8" r="4.2" fill="none" stroke="#fff" stroke-width="1"/><ellipse cx="8" cy="8" rx="1.8" ry="4.2" fill="none" stroke="#fff" stroke-width="1"/><path d="M3.8 8h8.4" stroke="#fff" stroke-width="1"/></svg>
        www.calverwickit.com.au
      </li>
    </ul>
  </section>

  <section class="card card-back" aria-label="Business card back">
    <div class="brand">
      <span class="brand-dot"></span>
      <span class="brand-name">calverwick tech</span>
    </div>
    <p class="tagline">We are an IT company specializing in Cloud Services<br>IT Managed Services, software and hardware</p>
    <p class="web">www.<span class="web-domain">calverwickit</span>.com.au</p>
  </section>
</main>
</body>
</html>
```